Internal Office Slogans / Motto / Vision Statements

Hi. We would like to put up some posters around the office with quotations such as -
-”Do what you do so well that they will want to see it again and bring their friends.”- Hollis Brandt
-Make your customers feel heard and understood. Make your customers feel respected and liked. Make your customers feel appreciated and helped. Understand that you can do none of these things unless you are sincere about them.
Terrence Oakley
- It’s a very predictable and satisfying phenomenon: whenever we get better, our customers do too.
Cal Pruett
-Catch people in the act of performing extraordinary customer service. Treat them like heroes. Tell their stories, far and wide.
Ned Farraday

The purpose of the posters is to reiterate our culture and vision within the organisation. They should be clean, crisp and eye catching, not gaudy or bright. Professional, bold and strong.

The company website and logo is at http://www.nexoraweb.com.au
Print size will be A1

Thanks for participating & looking forward to seeing your great work.
Updates

Hi All. . 

So to reiterate we are looking for one background design to be used for multiple quotes...  The list of quotes are as follows: 

Support and or Sales Office

 

Make your customers feel heard and understood.Make your customers feel respected and liked. Make your customers feelappreciated and helped. Understand that you can do none of these things unlessyou are sincere about them.

Terrence Oakley

 

Nothing liberates our greatness like the desireto help, the desire to serve

Dorothea Quill

 

It’s a very predictable and satisfying phenomenon:whenever we get better, our customers do too.

Cal Pruett

 

Success means we go to sleep at night knowingthat our talents and abilities were used in a way that served others.

Dorothea Quill.

 

The sole purpose of business is to create, serveand satisfy a customer, from beginning to end – and that’s everyone’s job.

Ned Farraday

 

We don’t celebrate closing a sale, we celebrateopening a relationship.

Rosalind Hext

I will never make you a promise – unless I giveyou a plan and procedure to make that promise possible.

Bo Tennant

 

Customers feel we take them for granted; onlyshow interest when we want an order; lavish our time on prospects; communicatemainly by invoice; are fixated on big accounts; drop them like hot potatoesonce we have the order; don’t follow through on promises; and satisfy our ownbureaucracy rather than their needs. We can do better than that, much better.

Alan P Merrow.

 

 

General and public area

 

Catch people in the act of performingextraordinary customer service. Treat them like heroes. Tell their stories, farand wide.

Ned Farraday

 

 

We see our customers as invited guests to aparty, and we are the hosts. It’s our job every day to make every importantaspect of the customer experience a little bit better." Carl Voight - Founder andCEO of Halverin

 

"If you do build a great experience,customers tell each other about that. Word of mouth is verypowerful."  Carl Voight

 

It's not a faithin technology. It's faith in people. Rick Palmer

 

“Being the richest man in the cemetery doesn’tmatter to me … Going to bed at night saying we’ve done something wonderful…that’s what matters to me.” Rick Palmer

 

The customer experience is the next competitivebattleground. Lance Morrow, CIO, Vantor Computers

 

”Do what you do so well that they will want tosee it again and bring their friends.”- Hollis Brandt

In the world of internet customer service, it isimportant to remember your competitor is only a mouse click away. FrankHolden (not sure who he is but like the quote).

The customer is why you go to work. If they goaway, you do, too. Peter Lindqvist (?)

 

MaybeSome for Sales or Build Team:

Quality is remembered long after the price is forgotten. Marzetti Family Slogan

```html
<!DOCTYPE html>
<html lang="en">
<head>
<meta charset="utf-8">
<title>Catch People in the Act – Ned Farraday</title>
<link rel="stylesheet" href="https://fonts.googleapis.com/css2?family=Jost:wght@300;400;500;700;800;900&family=Comfortaa:wght@500&display=swap">
<style>
  :root {
    --paper-top: #ede7db;
    --paper-bottom: #d5cab8;
    --ink: #2f2c29;
  }
  * { margin: 0; padding: 0; box-sizing: border-box; }
  html, body { width: 850px; height: 1200px; overflow: hidden; }
  body {
    background: linear-gradient(180deg, var(--paper-top) 0%, var(--paper-bottom) 100%);
    color: var(--ink);
    font-family: "Jost", sans-serif;
  }
  .poster { position: relative; width: 850px; height: 1200px; }
  .quote-line {
    position: absolute;
    left: 0; right: 0;
    text-align: center;
    text-transform: uppercase;
    line-height: 1;
    white-space: nowrap;
  }
  .quote-line strong { font-weight: 800; }
  .w-light { font-weight: 300; }
  .w-regular { font-weight: 400; }
  .w-medium { font-weight: 500; }
  .w-bold { font-weight: 700; }
  .w-heavy { font-weight: 800; }
  .w-black { font-weight: 900; letter-spacing: 2px; }

  .line-catch   { top: 56px;  font-size: 56px; }
  .line-act     { top: 158px; font-size: 56px; }
  .line-perform { top: 244px; font-size: 56px; }
  .line-extra   { top: 338px; font-size: 72px; letter-spacing: 1px; }
  .line-customer{ top: 441px; font-size: 72px; letter-spacing: 1px; }
  .line-service { top: 530px; font-size: 100px; }
  .line-treat   { top: 651px; font-size: 64px; }
  .line-heroes  { top: 734px; font-size: 88px; }
  .line-tell    { top: 850px; font-size: 58px; }
  .line-far     { top: 925px; font-size: 49px; }

  .divider { position: absolute; left: 0; top: 1031px; width: 850px; height: 6px; }

  .attribution {
    position: absolute;
    left: 0; right: 0;
    top: 1082px;
    text-align: center;
    font-family: "Comfortaa", sans-serif;
    font-weight: 500;
    font-size: 58px;
    line-height: 1;
    letter-spacing: 1px;
  }
</style>
</head>
<body>
  <main class="poster">
    <blockquote class="quote">
      <div class="quote-line line-catch w-regular">Catch People</div>
      <div class="quote-line line-act w-regular">In the <strong>Act</strong> of</div>
      <div class="quote-line line-perform w-medium">Performing</div>
      <div class="quote-line line-extra w-heavy">Extraordinary</div>
      <div class="quote-line line-customer w-black">Customer</div>
      <div class="quote-line line-service w-black">Service.</div>
      <div class="quote-line line-treat w-light">Treat them like</div>
      <div class="quote-line line-heroes w-black">Heroes.</div>
      <div class="quote-line line-tell w-light">Tell their <strong>Stories.</strong></div>
      <div class="quote-line line-far w-bold">Far and Wide.</div>
    </blockquote>

    <svg class="divider" viewBox="0 0 850 6" aria-hidden="true">
      <line x1="0" y1="3" x2="850" y2="3" stroke="var(--ink)" stroke-width="4" stroke-dasharray="6 3"/>
    </svg>

    <p class="attribution">-ned farraday</p>
  </main>
</body>
</html>
```